2021 Summer Ads Hollis Bay Custom Homes

We need a re-design of our summer ad run for our customer, Hollis Bay Custom Homes. They are custom home builders in the mostly rural parts of West Virginia, USA. They are known for their "Forever Home" tagline. We'd like two designed ads with the main difference being just the custom home that's featured. These designs should be for a Zintrola banner like 300 x 250 and square ad like 250 x 250. For inspiration please visit the Hollis Bay Custom Homes website at www dot hollisbaycustomhomes dot com

Target Market(s)

consumers / new home shoppers

Industry/Entity Type

Consumer

Requirements
Must have
• HBCH logo
Price Lock Available!
Custom home pic
Learn more >
small CFRM logo mark

```html
<!DOCTYPE html>
<html lang="en">
<head>
<meta charset="utf-8">
<title>Hollis Bay Custom Homes – Summer Ad</title>
<link rel="stylesheet" href="https://fonts.googleapis.com/css2?family=Montserrat:wght@500;600;700;800&family=Cinzel:wght@700&display=swap">
<style>
  :root {
    --navy: #1b1f2d;
    --navy-deep: #12141d;
    --red: #e0242f;
    --red-dark: #8f1119;
    --white: #ffffff;
    --sky-top: #8d8bb0;
    --sky-mid: #c8b7c2;
    --stone: #9a6f52;
    --ground: #6a4a38;
  }
  * { margin: 0; padding: 0; box-sizing: border-box; }
  html, body { width: 1200px; height: 1000px; overflow: hidden; background: var(--navy); }
  .ad {
    position: relative;
    width: 1200px;
    height: 1000px;
    overflow: hidden;
    background: var(--navy);
    font-family: "Montserrat", Arial, sans-serif;
    color: var(--white);
  }
  .ad-shapes { position: absolute; inset: 0; }
  .brand {
    position: absolute;
    left: 80px;
    top: 96px;
    width: 400px;
    text-align: center;
    font-family: "Cinzel", Georgia, serif;
    font-weight: 700;
    color: var(--white);
    line-height: 1;
  }
  .brand-name { display: block; font-size: 50px; letter-spacing: 1px; }
  .brand-sub { display: block; font-size: 22px; letter-spacing: 6px; margin-top: 12px; }
  .headline {
    position: absolute;
    left: 80px;
    top: 292px;
    text-transform: uppercase;
    line-height: 1.2;
  }
  .headline-lead { display: block; font-size: 54px; font-weight: 500; letter-spacing: 1px; }
  .headline-main { display: block; font-size: 60px; font-weight: 800; }
  .price-lock {
    position: absolute;
    left: 82px;
    top: 534px;
    font-size: 31px;
    font-weight: 700;
    text-transform: uppercase;
    letter-spacing: 0.5px;
  }
  .cta {
    position: absolute;
    left: 80px;
    top: 616px;
    width: 330px;
    height: 94px;
    border-radius: 10px;
    background: var(--red);
    display: flex;
    align-items: center;
    padding-left: 42px;
    font-size: 28px;
    font-weight: 700;
    text-transform: uppercase;
    letter-spacing: 0.5px;
    overflow: hidden;
  }
  .cta-arrow {
    position: absolute;
    right: 0;
    top: 0;
    width: 94px;
    height: 94px;
    border-radius: 50% 10px 10px 50%;
    background: var(--red-dark);
    display: flex;
    align-items: center;
    justify-content: center;
  }
  .member {
    position: absolute;
    left: 74px;
    top: 790px;
    line-height: 1.1;
  }
  .member-name { display: block; font-size: 64px; font-weight: 800; letter-spacing: 1px; }
  .member-sub { display: block; font-size: 21px; font-weight: 500; margin-top: 8px; }
</style>
</head>
<body>
<main class="ad">
  <svg class="ad-shapes" width="1200" height="1000" viewBox="0 0 1200 1000">
    <defs>
      <linearGradient id="photoFill" x1="0" y1="0" x2="0" y2="1">
        <stop offset="0" stop-color="var(--sky-top)"/>
        <stop offset="0.35" stop-color="var(--sky-mid)"/>
        <stop offset="0.7" stop-color="var(--stone)"/>
        <stop offset="1" stop-color="var(--ground)"/>
      </linearGradient>
      <linearGradient id="redBand" x1="0" y1="0" x2="1" y2="1">
        <stop offset="0" stop-color="var(--red)"/>
        <stop offset="1" stop-color="var(--red-dark)"/>
      </linearGradient>
    </defs>
    <polygon class="ad-shade" points="0,0 520,0 0,620" fill="var(--navy-deep)" opacity="0.55"/>
    <polygon class="accent-top" points="380,0 640,0 470,210" fill="url(#redBand)" opacity="0.9"/>
    <polygon class="accent-band" points="790,0 900,0 520,1000 410,1000" fill="url(#redBand)"/>
    <polygon class="home-photo" role="img" aria-label="Photo of a white custom home with a blue metal roof, screened porch and stone columns at dusk"
             points="880,0 1200,0 1200,1000 500,1000" fill="url(#photoFill)"/>
  </svg>

  <div class="brand">
    <span class="brand-name">HOLLIS BAY</span>
    <span class="brand-sub">CUSTOM HOMES</span>
  </div>

  <h1 class="headline">
    <span class="headline-lead">Start Building</span>
    <span class="headline-main">Your Forever</span>
    <span class="headline-main">Home Today!</span>
  </h1>

  <p class="price-lock">Price Lock Available!</p>

  <a class="cta">Learn More
    <span class="cta-arrow">
      <svg width="30" height="40" viewBox="0 0 30 40"><polyline points="8,6 22,20 8,34" fill="none" stroke="var(--white)" stroke-width="7" stroke-linecap="round" stroke-linejoin="round"/></svg>
    </span>
  </a>

  <div class="member">
    <span class="member-name">CFRM</span>
    <span class="member-sub">Council for<br>Residential Makers</span>
  </div>
</main>
</body>
</html>
```